New Fun, Positive, energised looking Business Card Needed for High Achiever Coach

I am looking for a two sided full colour business card. I am self employed and have recently re branded my 1-2-1 work re-vitalising high achievers. My target client base for these cards is therefore high achievers - usually aged 40 -55, they are often entrepreneurs, CEO or work in banking and finance and 2/3 are male. I work with them on 90 day or 6 month coaching programs to help them live their success in a healthier, more sustainable and fulfiiled way. They pay for this privately so though they are corporate types the cards need not look 'corporate'. I want to portray the idea of transformation, vitality and re-connecting.
You can get a feel for the look I like on my new website: morvenlisk.co.uk
I want to use this logo with strapline (Re-Vitalising High Achievers) (I purchased off Logoharbor) and font/ colours (the turquoise and green).
Details to include on the card:
www.morvenlisk.co.uk
+44 7915 302618
morven@morvenlisk.co.uk
skype: morvenlisk
I'd also like to include:
Do you struggle to switch off? Want to be healthier and feel fitter? Want closer relationships? More clarity over the direction you are headed? I can help you do these things using integrated mind-body techniques. Visit morvenlisk.co.uk TODAY to apply for a FREE Breakthrough session.
BUT if that is too much text for a card I am open to advice/ammendments.
Updates
Thanks for your design - I am considering them. PLease change the wording to :

```html
<!DOCTYPE html>
<html lang="en">
<head>
<meta charset="utf-8">
<title>Morven Lisk – Business Card</title>
<link rel="stylesheet" href="https://fonts.googleapis.com/css2?family=Open+Sans:wght@400;700&display=swap">
<style>
  :root {
    --backdrop: #4a4a4a;
    --card-white: #ffffff;
    --turquoise: #1a9cc4;
    --turquoise-light: #0fb0d6;
    --turquoise-dark: #0c7fa6;
    --leaf-green: #5cbb6a;
    --ink: #1e1e1e;
  }
  * { box-sizing: border-box; margin: 0; padding: 0; }
  html, body { width: 1200px; height: 900px; overflow: hidden; }
  body {
    background: var(--backdrop);
    display: flex;
    align-items: center;
    justify-content: center;
    gap: 40px;
    font-family: "Open Sans", sans-serif;
  }
  .card {
    position: relative;
    width: 540px;
    height: 348px;
    border-radius: 22px;
    overflow: hidden;
    box-shadow: 0 6px 18px rgba(0,0,0,0.35);
  }

  /* Front */
  .card-front { background: var(--card-white); }
  .brand-dot {
    position: absolute;
    left: 88px; top: 50px;
    width: 110px; height: 110px;
    border-radius: 50%;
    background: var(--leaf-green);
  }
  .brand-name {
    position: absolute;
    left: 32px; top: 182px;
    font-family: "Open Sans", sans-serif;
    font-weight: 700;
    font-size: 34px;
    line-height: 1;
    color: var(--turquoise);
  }
  .strapline {
    position: absolute;
    left: 34px; top: 226px;
    font-family: "Open Sans", sans-serif;
    font-size: 16px;
    line-height: 1;
    color: var(--turquoise);
  }
  .divider {
    position: absolute;
    left: 292px; top: 184px;
    width: 1.5px; height: 88px;
    background: var(--turquoise);
  }
  .contact-list {
    position: absolute;
    left: 306px; top: 186px;
    list-style: none;
    font-size: 14px;
    color: var(--ink);
  }
  .contact-list li {
    display: flex; align-items: center; gap: 9px;
    height: 21px;
  }
  .contact-list svg { width: 14px; height: 14px; flex: none; }
  .contact-list .plain-dot {
    width: 12px; height: 12px; border-radius: 50%;
    background: var(--turquoise); flex: none; margin: 0 1px;
  }
  .front-wave {
    position: absolute; left: 0; bottom: 0;
    width: 540px; height: 90px;
  }

  /* Back */
  .card-back {
    background: radial-gradient(ellipse at 55% 35%, var(--turquoise-light) 0%, var(--turquoise) 45%, var(--turquoise-dark) 100%);
    color: #ffffff;
  }
  .back-mark {
    position: absolute;
    left: 0; right: 0; top: 66px;
    display: flex; align-items: center; justify-content: center; gap: 12px;
    font-weight: 700;
    font-size: 30px;
    color: #ffffff;
  }
  .back-mark .dot {
    width: 22px; height: 22px; border-radius: 50%;
    background: #ffffff;
  }
  .pitch {
    position: absolute;
    left: 22px; right: 22px; top: 190px;
    text-align: center;
    font-size: 12.6px;
    line-height: 1.45;
  }
  .pitch .call-to-action { font-weight: 700; font-size: 13.4px; }
</style>
</head>
<body>

  <section class="card card-front" aria-label="Business card front">
    <span class="brand-dot" aria-hidden="true"></span>
    <h1 class="brand-name">Morven Lisk</h1>
    <p class="strapline">Renewing Driven Leaders</p>
    <div class="divider"></div>
    <ul class="contact-list">
      <li>
        <svg viewBox="0 0 16 16" aria-hidden="true"><path fill="var(--turquoise)" d="M3.5 1.5l2.3 0 1 3.2-1.5 1.2a8 8 0 0 0 4.8 4.8l1.2-1.5 3.2 1v2.3c0 .8-.7 1.5-1.5 1.5A12 12 0 0 1 2 3c0-.8.7-1.5 1.5-1.5z"/></svg>
        +44 7915 302618
      </li>
      <li>
        <svg viewBox="0 0 16 16" aria-hidden="true"><circle cx="8" cy="8" r="6.5" fill="none" stroke="var(--turquoise)" stroke-width="1.5"/><path d="M1.5 8h13M8 1.5c-3 3.5-3 9.5 0 13M8 1.5c3 3.5 3 9.5 0 13" fill="none" stroke="var(--turquoise)" stroke-width="1.2"/></svg>
        www.morvenlisk.co.uk
      </li>
      <li>
        <svg viewBox="0 0 16 16" aria-hidden="true"><rect x="1.5" y="3.5" width="13" height="9" rx="1" fill="var(--turquoise)"/><path d="M1.5 4l6.5 5 6.5-5" fill="none" stroke="#fff" stroke-width="1.2"/></svg>
        morven@morvenlisk.co.uk
      </li>
      <li>
        <span class="plain-dot"></span>
        morvenlisk
      </li>
    </ul>
    <svg class="front-wave" viewBox="0 0 540 90" preserveAspectRatio="none" aria-hidden="true">
      <defs>
        <linearGradient id="bandGreen" x1="0" y1="0" x2="1" y2="0">
          <stop offset="0" stop-color="#2f8a3a"/>
          <stop offset="0.5" stop-color="#5cbb6a"/>
          <stop offset="1" stop-color="#2f8a3a"/>
        </linearGradient>
      </defs>
      <path d="M0 30 C150 10 300 20 420 40 C470 48 510 46 540 40 L540 90 L0 90 Z" fill="url(#bandGreen)"/>
      <path d="M0 22 C120 2 260 6 400 26 C460 34 500 36 540 30 C500 42 460 44 400 38 C260 18 120 14 0 30 Z" fill="var(--turquoise)"/>
    </svg>
  </section>

  <section class="card card-back" aria-label="Business card back">
    <div class="back-mark"><span class="dot"></span>Morven Lisk</div>
    <p class="pitch">
      Do you struggle to switch off? Want to be healthier and feel fitter? Want closer
      relationships? More clarity over the direction you are headed? I can help you do
      these things using integrated mind-body techniques.<br>
      <span class="call-to-action">Visit morvenlisk.co.uk TODAY to apply for a FREE Breakthrough session.</span>
    </p>
  </section>

</body>
</html>
```